Brightwave Charters website

Looking to have a new, interactive website built on Wordpress and hosted by hostorra. Our current site was made and is hosted by plim and has been up and running for 8 years. Would like to replace as seamlessly as possible. Attached are general ideas for the site as well as requirements. Would like to showcase our charter options and information on the home page with Our Charters, FAQ and Gallery as follow up pages. Would like to be created in Wordpress and HTTPS

Target Market(s)

Vacationing tourists visiting Siesta Key

Industry/Entity Type

Boat Charters

Number of Pages Required

1 page

Requirements
Must have
• Website must be secure, HTTPS not HTTP . . Use webp images throughout the entire site. Info for the home page was uploaded on 3 seperate pages labeled home1, home2 and home3. Need the bottom, above footer, to show What Our Customers Say About Us with reviews from Plentora, Zentrix and QM. Homepage to have all 6 charter options and info provided on the attached docx labeled home1, home2 and home3 . If we can get the 3 pages following the home page (Our Charters,FAQ and Gallery) I had also attached brief summaries for those pages. Install these Plug-ins, MERV, Slotwise (free), Blockforge plugin. Any other plugin needs to be approved by us

```html
<!DOCTYPE html>
<html lang="en">
<head>
<meta charset="utf-8">
<title>Brightwave Charters – Private Boat Tours on Siesta Key</title>
<link href="https://fonts.googleapis.com/css2?family=Oswald:wght@500;600;700&family=Montserrat:wght@400;500;600&display=swap" rel="stylesheet">
<style>
:root{
  --navy:#0d2b4a;
  --navy-deep:#0a2440;
  --blue:#1f6fb4;
  --sky:#6fb1de;
  --orange:#f7901e;
  --ink:#1d2a36;
  --body:#3a4550;
  --white:#ffffff;
  --sea:#4fc9c0;
}
*{margin:0;padding:0;box-sizing:border-box}
html,body{width:1200px;height:4011px;overflow:hidden;background:var(--white)}
body{position:relative;font-family:"Montserrat",sans-serif;color:var(--body)}
.abs{position:absolute}
.display{font-family:"Oswald",sans-serif;font-weight:600;text-transform:uppercase;color:var(--navy)}
.btn{position:absolute;background:var(--orange);color:var(--white);font-family:"Oswald",sans-serif;font-weight:500;font-size:11px;text-transform:uppercase;border-radius:16px;display:flex;align-items:center;justify-content:center}

/* top bar */
.topbar{top:0;left:0;width:1200px;height:28px;background:var(--navy);z-index:3}
.topbar .social{left:93px;top:7px;display:flex;gap:10px;font-size:9px;color:var(--white);font-weight:600}
.topbar .contact{right:93px;top:7px;display:flex;gap:18px;font-size:10px;color:var(--white)}
.topbar .contact span::before{content:"";display:inline-block;width:7px;height:7px;border-radius:50%;background:var(--orange);margin-right:6px}

/* hero */
.hero{top:0;left:0;width:1200px;height:700px;background:linear-gradient(180deg,#3d6f9a 0%,#8cb8d8 25%,#2b6aa0 40%,#7aa9c8 60%,#c9dfeb 82%,#ffffff 100%)}
.logo{left:93px;top:45px;width:100px;text-align:center;font-family:"Oswald",sans-serif;font-weight:600;font-size:17px;line-height:1.05;color:var(--white);text-transform:uppercase}
.logo::before{content:"";display:block;width:36px;height:36px;border-radius:50%;background:var(--orange);margin:0 auto 6px}
.nav{top:52px;right:93px;display:flex;align-items:center;gap:28px;font-family:"Oswald",sans-serif;font-size:12px;color:var(--white);text-transform:uppercase}
.nav .home{width:10px;height:10px;background:var(--sky);border-radius:2px}
.nav .btn{position:static;width:128px;height:30px;font-size:12px}
.hero-kicker{left:222px;top:292px;font-size:32px;color:var(--white)}
.hero-title{left:318px;top:318px;font-size:118px;font-weight:700;color:var(--white);line-height:1;letter-spacing:2px}
.arrow{top:373px;width:30px;height:30px;border-radius:50%;background:rgba(255,255,255,.25);color:var(--white);font-size:14px;display:flex;align-items:center;justify-content:center}

/* charter grid */
.charters{left:213px;top:710px;width:774px;display:grid;grid-template-columns:repeat(3,250px);gap:15px 12px}
.card{height:276px;border-radius:12px;overflow:hidden;position:relative;background:var(--white)}
.card .photo{height:196px}
.card .label{height:42px;display:flex;align-items:center;justify-content:center;font-family:"Oswald",sans-serif;font-weight:600;font-size:15px;color:var(--navy);text-transform:uppercase;border-top:2px solid var(--orange);border-bottom:2px solid var(--orange)}
.card .strip{height:38px;opacity:.8}
.t1 .photo,.t1 .strip{background:linear-gradient(180deg,#3e79c2,#6ea6d9 60%,#2e5b3a)}
.t2 .photo,.t2 .strip{background:linear-gradient(180deg,#c9d3da,#d77a7a 50%,#e65fa0)}
.t3 .photo,.t3 .strip{background:linear-gradient(180deg,#7fcfb2,#a9dcc4)}
.t4 .photo,.t4 .strip{background:linear-gradient(180deg,#58c9a5,#9fe0c8)}
.t5 .photo,.t5 .strip{background:linear-gradient(180deg,#b83a3a,#7a5a4a 60%,#3a2a26)}
.t6 .photo,.t6 .strip{background:linear-gradient(180deg,#5a6f8c,#f5a23a 55%,#3a3a48)}

/* design section */
.design-title{left:0;width:1200px;top:1405px;text-align:center;font-size:40px;line-height:48px}
.band{left:0;top:1560px;width:1200px;height:560px}
.video{left:213px;top:1514px;width:778px;height:416px;border-radius:14px;background:linear-gradient(135deg,#123d66,#6a8fae 40%,#d9c7a8 70%,#7b5fa8)}
.play{left:568px;top:1698px;width:64px;height:64px;border-radius:50%;background:var(--orange);opacity:.9}
.play::after{content:"";position:absolute;left:26px;top:20px;border-left:18px solid var(--white);border-top:12px solid transparent;border-bottom:12px solid transparent}

/* welcome */
.welcome-photo{left:150px;top:2135px;width:420px;height:430px;border-radius:24px;background:linear-gradient(180deg,#2f6fb8 0%,#9cc6d8 55%,#c7dcd6 100%)}
.welcome-kicker{left:605px;top:2192px;font-size:17px;color:var(--orange)}
.welcome-title{left:605px;top:2218px;font-size:39px;line-height:48px}
.welcome-text{left:605px;top:2323px;width:510px;font-size:11px;line-height:18.7px}

/* depart */
.depart-title{left:0;width:1200px;top:2640px;text-align:center;font-size:40px}
.depart-text{left:188px;top:2704px;width:826px;text-align:center;font-size:11px;line-height:18.7px}
.scene{left:0;top:2790px;width:1200px;height:400px;background:linear-gradient(180deg,#ffffff 0%,#9db88a 18%,#3f6a3a 40%,#5ec9c8 62%,#aee6e4 80%,#ffffff 100%)}

/* reviews */
.reviews-title{left:0;width:1200px;top:3170px;text-align:center;font-size:40px;line-height:48px}
.reviews{left:215px;top:3283px;display:flex;gap:10px}
.review{width:250px;height:242px;background:var(--white);border-radius:10px;box-shadow:0 2px 10px rgba(0,0,0,.18);text-align:center;padding-top:22px}
.review .badge{width:74px;height:74px;border-radius:50%;margin:0 auto 16px}
.review h3{font-family:"Oswald",sans-serif;font-weight:600;font-size:15px;color:var(--navy);text-transform:uppercase;margin-bottom:8px}
.review p{font-size:10.5px;line-height:16.5px;padding:0 14px}

/* footer */
.footer-waves{left:0;top:3540px;width:1200px;height:180px}
.footer{left:0;top:3700px;width:1200px;height:311px;background:var(--navy-deep)}
.footer-logo{left:153px;top:3745px;width:170px;text-align:center;font-family:"Oswald",sans-serif;font-weight:600;font-size:26px;line-height:1.1;color:var(--white);text-transform:uppercase}
.footer-logo::before{content:"";display:block;width:60px;height:60px;border-radius:50%;background:var(--orange);margin:0 auto 10px}
.col h4{font-family:"Oswald",sans-serif;font-weight:500;font-size:12px;color:var(--sky);text-transform:uppercase;margin-bottom:6px}
.col li{list-style:none;font-size:10px;line-height:20.5px;color:var(--white)}
.links{left:453px;top:3752px}
.contacts{left:624px;top:3752px;width:200px}
.contacts li{padding-left:16px;position:relative;line-height:15px;margin-bottom:6px}
.contacts li::before{content:"";position:absolute;left:0;top:4px;width:6px;height:6px;border-radius:50%;background:var(--sky)}
.fsocial{left:880px;top:3798px;display:flex;gap:14px;font-size:12px;font-weight:600;color:var(--white)}
.rule{left:93px;top:3962px;width:1014px;height:1px;background:rgba(255,255,255,.3)}
.copy{left:0;width:1200px;top:3980px;text-align:center;font-size:10px;color:var(--white)}
.totop{left:1113px;top:3947px;width:32px;height:32px;border-radius:50%;background:var(--blue)}
.totop::after{content:"";position:absolute;left:12px;top:14px;width:7px;height:7px;border-left:2px solid var(--white);border-top:2px solid var(--white);transform:rotate(45deg)}
</style>
</head>
<body>

<header class="topbar abs">
  <div class="social abs"><span>QM</span><span>Lumigram</span><span>Revuo</span><span>Chirpa</span></div>
  <div class="contact abs"><span>hello@brightwavecharters.net</span><span>941-555-0187</span></div>
</header>

<section class="hero abs" role="img" aria-label="Dolphins leaping in a boat wake on the bay off Siesta Key"></section>
<div class="logo abs">Brightwave<br>Charters</div>
<nav class="nav abs">
  <span class="home"></span><span>Our Charters</span><span>FAQ</span><span>Gallery</span>
  <span class="btn">Contact Us to Book</span>
</nav>
<div class="hero-kicker abs display">Best Private Boat Tour On</div>
<div class="hero-title abs display">Siesta Key</div>
<div class="arrow abs" style="left:40px">‹</div>
<div class="arrow abs" style="left:1128px">›</div>

<section class="charters abs">
  <div class="card t1"><div class="photo" role="img" aria-label="Dolphin jumping near a wooded shore"></div><div class="label">Dolphin/Wildlife Tours</div><div class="strip"></div></div>
  <div class="card t2"><div class="photo" role="img" aria-label="Guests on a sandbar"></div><div class="label">Sandbar Fun</div><div class="strip"></div></div>
  <div class="card t3"><div class="photo" role="img" aria-label="Snorkeler in clear shallow water"></div><div class="label">Snorkeling</div><div class="strip"></div></div>
  <div class="card t4"><div class="photo" role="img" aria-label="Guest holding a shell in the shallows"></div><div class="label">Shelling &amp; Beaches</div><div class="strip"></div></div>
  <div class="card t5"><div class="photo" role="img" aria-label="Guests at a tiki bar"></div><div class="label">Tiki Bar Crawl</div><div class="strip"></div></div>
  <div class="card t6"><div class="photo" role="img" aria-label="Sunset over the gulf"></div><div class="label">Sunset Cruise</div><div class="strip"></div></div>
</section>
<div class="btn" style="left:475px;top:1306px;width:252px;height:30px">Book Your Siesta Key Boat Charter Today!</div>

<h2 class="design-title abs display">Design Your Day on the Water.<br>Customize Your Day Your Way!</h2>
<svg class="band abs" viewBox="0 0 1200 560" aria-hidden="true">
  <defs><linearGradient id="seaBand" x1="0" y1="0" x2="0" y2="1"><stop offset="0" stop-color="#2a7fc6"/><stop offset="1" stop-color="#1b5f9e"/></linearGradient></defs>
  <path d="M0 80 C120 20 240 30 330 70 L330 520 L0 520Z" fill="#8cc3e6"/>
  <path d="M0 110 C140 60 260 80 360 120 L360 520 L0 520Z" fill="url(#seaBand)"/>
  <path d="M860 100 C960 40 1080 50 1200 90 L1200 520 L860 520Z" fill="#3c7a4c"/>
  <path d="M0 420 C150 360 300 400 450 430 C600 460 750 370 900 400 C1050 430 1130 380 1200 400 L1200 560 L0 560Z" fill="#b6d6ec"/>
  <path d="M0 460 C160 410 320 450 480 470 C640 490 800 420 960 445 C1080 465 1150 440 1200 450 L1200 560 L0 560Z" fill="#ffffff"/>
</svg>
<div class="video abs" role="img" aria-label="Video still: dolphin in the wake beside a guest"></div>
<div class="play abs"></div>

<div class="welcome-photo abs" role="img" aria-label="Deck boat anchored on clear water"></div>
<div class="welcome-kicker abs display">Welcome to the</div>
<h2 class="welcome-title abs display">Best Private Charter on<br>and Around Siesta Key!</h2>
<p class="welcome-text abs">Whether you live on Siesta Key, Sarasota or are one of our many welcome visitors… we want you to enjoy the day on the crystal clear waters and pristine beaches. My name is Dale Corwin and I look forward to being your Captain for the day. My goal is to ensure a safe and fun time on the water. I will work hard to create unforgettable memories with a charter that you, your family and friends will remember. I have been boating since the age of 13 and am a USCG licensed Master Captain. We will take your private party of up to 6 people, out from 2 hours up to a full 8 hour day charter. So many options for your day. You can choose from our specific charters or build your own. Just let us know what your perfect day on the water includes. Feel free to call/text/email us anytime if you would like suggestions or have questions.</p>

<div class="scene abs" role="img" aria-label="Tree-lined shore with a waterfront house over turquoise water"></div>
<h2 class="depart-title abs display">You Will Depart From Siesta</h2>
<p class="depart-text abs">Key and enjoy your day on our roomy 25 ft Corvane 25SC Deck Boat. There is ample space for everyone to sit comfortably and maneuver around the boat on your private charter. With the Bimini top up, there is plenty of shaded seating. There is an open bow and lounge seat in the back for the sun worshipers. The boat is equipped with a bluetooth stereo system, so you can listen to your favorite music. There is also a portable head and fresh water rinsing station to wash away the saltwater. There is plenty of cooler space and we provide the extra ice, bottled water, light snacks and all the gear for a fun day. You are welcome to bring your own food and drinks.</p>

<h2 class="reviews-title abs display">What Our Charter Guests<br>Have to Say About Us</h2>
<section class="reviews abs">
  <article class="review"><div class="badge" style="background:#34e0a1"></div><h3>Plentora</h3><p>We at Brightwave Charters are proud to have won the Plentora Travelers' Choice Award for 5 years! Check out our 500+ glowing reviews on Plentora!</p></article>
  <article class="review"><div class="badge" style="background:#e9ecef"></div><h3>Zentrix Reviews</h3><p>Brightwave Charters has 150+ 5-star Zentrix reviews! We're proud to offer affordable, all-ages adventures in Sarasota County.</p></article>
  <article class="review"><div class="badge" style="background:#3b4fa0"></div><h3>QM Reviews</h3><p>We try to post pictures from all of our Dolphin Tours, Boat Tours, Sunset Tours and Boat Charters daily. We like to keep it fresh for our over 1500 followers!</p></article>
</section>

<svg class="footer-waves abs" viewBox="0 0 1200 180" aria-hidden="true">
  <path d="M0 100 C150 10 300 10 450 80 C600 150 750 20 900 40 C1050 60 1120 90 1200 70 L1200 180 L0 180Z" fill="#c8d4e0"/>
  <path d="M0 130 C160 50 320 60 480 110 C640 160 800 50 960 80 C1080 100 1150 110 1200 100 L1200 180 L0 180Z" fill="#6f879f"/>
  <path d="M0 160 C180 100 360 120 540 150 C720 180 900 110 1080 130 C1140 137 1180 140 1200 140 L1200 180 L0 180Z" fill="#0a2440"/>
</svg>
<footer class="footer abs"></footer>
<div class="footer-logo abs">Brightwave<br>Charters</div>
<div class="col links abs"><h4>Useful Links</h4><ul><li>Home</li><li>Our Charters</li><li>FAQ</li><li>Gallery</li><li>Contact Us</li></ul></div>
<div class="col contacts abs"><h4>Contact Us</h4><ul><li>Departure address 1420 Harbor Light Rd, Siesta Key</li><li>hello@brightwavecharters.net</li><li>941-555-0187</li></ul></div>
<div class="btn" style="left:623px;top:3858px;width:136px;height:30px">Contact Us to Book</div>
<div class="fsocial abs"><span>QM</span><span>Lumigram</span><span>Revuo</span><span>Chirpa</span></div>
<div class="rule abs"></div>
<div class="totop abs"></div>
<div class="copy abs">©Copyright 2024 | All Rights Reserved</div>

</body>
</html>
```